DESKHAVEN COSPACE Website design and coding

DESKHAVEN COSPACE

DESKHAVEN is Harborview’s first (and currently only) shared business co-working space. We share the same upscale, casual work environment, but we work independently on our own (or our team’s) projects and goals. For only a flat $195 membership fee per month, you have your very own all-inclusive, fun, personal business office environment. Website is written (Word file #12, below); and all pictures etc provided. Harborview is a beachy, coastal, historic city an hour from Houston, Texas USA. Logo (file 11 below) is temporary only.

Target Market(s)

Outside sales people, medical students looking for study hall, Houston companies looking for local office, real estate agents, graphic artists, entrepreneurs, etc

Contact Information for Business Card

will discuss --want to combine with current business card with multiple businesses

Logo Text

DESKHAVEN COSPACE

Coding

Coded - Design and coding required

Number of Pages Required

5+ page

Colors
ec1f27
fbed22

Requirements
Nice to have
• maroon/wine dominant with yellow and red accents, gray base are the colors of the space--website could coordinate--but open to creative ideas/combinations

```html
<!DOCTYPE html>
<html lang="en">
<head>
<meta charset="utf-8">
<title>Amenities – Deskhaven Cospace</title>
<link href="https://fonts.googleapis.com/css2?family=Fira+Sans:wght@400;600;700&family=Hind:wght@400;500;600&family=Playfair+Display:wght@700;800&display=swap" rel="stylesheet">
<style>
:root{
  --wine:#8a0000;
  --wine-dark:#6e0000;
  --gold:#fcd600;
  --base:#f3f3f3;
  --band:#e6e6e6;
  --ink:#333;
  --white:#fff;
}
*{box-sizing:border-box;margin:0;padding:0}
html,body{width:1200px;height:1200px;overflow:hidden;background:var(--white)}
body{font-family:"Hind",sans-serif;color:var(--ink)}
.page{position:absolute;left:366px;top:0;width:754px;height:1932px;transform:scale(0.6211);transform-origin:0 0;background:var(--base);overflow:hidden}
.abs{position:absolute}
.heading{font-family:"Fira Sans",sans-serif;color:var(--wine);line-height:1.2}
.heading b{font-weight:700}
.heading span{font-weight:400}
.rule{position:absolute;height:2px;width:55px;background:var(--gold)}
.num{position:absolute;font-family:"Playfair Display",serif;font-weight:800;color:var(--wine);font-size:44px;line-height:1}
.photo{position:absolute}

.nav{position:absolute;left:0;top:0;width:754px;height:38px;background:var(--wine)}
.brand{position:absolute;left:70px;top:12px;font-family:"Fira Sans",sans-serif;font-size:11px;color:var(--gold);letter-spacing:.2px}
.brand b{font-weight:700}
.nav-links{position:absolute;top:14px;left:0;font-size:8.5px;color:var(--white)}
.nav-links a{position:absolute;white-space:nowrap;color:inherit;text-decoration:none}
.nav-links a.active{color:var(--gold);border-bottom:1.5px solid var(--gold);padding-bottom:2px}

.hero{position:absolute;left:0;top:38px;width:754px;height:204px;background:linear-gradient(100deg,#5a4630 0%,#4a4848 40%,#3d4046 60%,#5c5a54 100%)}
.hero-shade{position:absolute;inset:0;background:rgba(0,0,0,.15)}
.hero-title{position:absolute;top:68px;width:100%;text-align:center;font-family:"Fira Sans",sans-serif;font-weight:600;font-size:25px;color:var(--white)}
.crumbs{position:absolute;top:118px;width:100%;text-align:center;font-size:8px;color:var(--white)}
.crumbs .home{color:var(--gold)}

.ticks{position:absolute;list-style:none;font-size:8px;line-height:15px}
.ticks li{position:relative;padding-left:18px}
.ticks li svg{position:absolute;left:0;top:3px;width:9px;height:9px}
.dots{position:absolute;list-style:none;font-size:8px;line-height:13px}
.dots li{margin-bottom:6px}
.dots li::before{content:"•";color:var(--wine);margin-right:6px}

.cta{position:absolute;left:0;top:1488px;width:754px;height:215px;background:var(--band);text-align:center}
.cta-title{position:absolute;top:30px;width:100%;font-family:"Fira Sans",sans-serif;font-weight:600;font-size:27px;color:var(--wine)}
.cta-text{position:absolute;top:98px;width:100%;font-family:"Hind",sans-serif;font-size:10.5px;line-height:13px;color:#444}
.btn{position:absolute;left:312px;top:156px;width:110px;height:26px;border-radius:13px;background:var(--wine);color:var(--white);font-family:"Fira Sans",sans-serif;font-weight:600;font-size:8px;line-height:26px}

.footer{position:absolute;left:0;top:1703px;width:754px;height:229px;background:var(--wine);color:var(--white)}
.f-brand{position:absolute;left:71px;top:36px;font-family:"Fira Sans",sans-serif;font-size:13px;line-height:14px;color:var(--gold)}
.f-brand b{font-weight:700}
.f-map{position:absolute;left:33px;top:80px;width:140px;height:75px;background:rgba(255,255,255,.07);border-radius:6px}
.f-tag{position:absolute;left:71px;top:80px;font-size:8px;line-height:15px}
.f-copy{position:absolute;left:75px;top:144px;font-size:4.5px;line-height:11px;color:var(--white)}
.f-copy span{color:var(--gold)}
.f-head{position:absolute;top:40px;font-family:"Fira Sans",sans-serif;font-weight:600;font-size:9.5px;color:var(--gold)}
.f-list{position:absolute;top:80px;list-style:none;font-size:8px;line-height:15px}
.f-list .on{color:var(--gold)}
</style>
</head>
<body>
<svg width="0" height="0" style="position:absolute">
  <symbol id="tick" viewBox="0 0 10 10"><circle cx="5" cy="5" r="5" fill="#8a0000"/><path d="M2.8 5.2l1.5 1.5 3-3.2" fill="none" stroke="#fff" stroke-width="1.2"/></symbol>
</svg>
<main class="page">

  <header class="nav">
    <div class="brand"><b>DESKHAVEN</b> COSPACE</div>
    <nav class="nav-links">
      <a style="left:429px">Home</a>
      <a style="left:474px">About</a>
      <a class="active" style="left:520px">Amenities</a>
      <a style="left:583px">Membership</a>
      <a style="left:653px">Contact</a>
    </nav>
  </header>

  <section class="hero" role="img" aria-label="Dim photo of the lounge with tables, lockers and a white sofa">
    <div class="hero-shade"></div>
    <h1 class="hero-title">Amenities</h1>
    <div class="crumbs"><span class="home">Home</span> &nbsp;→&nbsp; Amenities</div>
  </section>

  <div class="abs" style="left:107px;top:303px;width:246px;height:194px;border:5px solid var(--gold)"></div>
  <div class="photo" role="img" aria-label="Photo of three colleagues meeting at a table" style="left:71px;top:328px;width:256px;height:193px;background:linear-gradient(120deg,#6d5a4b,#cfc5b8 45%,#9b8a7a)"></div>
  <h2 class="heading abs" style="left:385px;top:338px;font-size:27px"><b>Our Working Spaces</b><br><span>Have Everything You Need</span></h2>
  <div class="rule" style="left:385px;top:410px"></div>
  <p class="abs" style="left:385px;top:429px;width:280px;font-size:8px;line-height:13px">DESKHAVEN is the first Harborview co-working space, and offers all of the following features, all included in your monthly $195 membership fee:</p>

  <div class="num" style="left:71px;top:572px">01</div>
  <div class="rule" style="left:71px;top:622px"></div>
  <h3 class="heading abs" style="left:71px;top:632px;font-size:17px"><b>Great</b> <span>Location</span></h3>
  <ul class="ticks" style="left:71px;top:669px;width:300px">
    <li style="margin-bottom:14px"><svg><use href="#tick"/></svg>Great modern design – a place that looks “cutting edge” and which you will be proud to call your own.</li>
    <li style="margin-bottom:14px"><svg><use href="#tick"/></svg>Building is a fabulous example of Mid-Century Modern architecture – lots of glass, open and light with luxurious granite floors and crisp Mid-Mod design.</li>
    <li><svg><use href="#tick"/></svg>Great location – a block from Harborview’s Mercer Row area of coffee bars, restaurants, bars, art galleries, and the 1894 Lyric Hall.</li>
  </ul>
  <div class="photo" role="img" aria-label="Photo of the red brick building on a street corner" style="left:385px;top:580px;width:298px;height:200px;background:linear-gradient(180deg,#dfe6ec 0%,#b5614a 45%,#9a4b38 70%,#a9a9a6 100%)"></div>

  <div class="num" style="left:230px;top:856px">02</div>
  <div class="rule" style="left:230px;top:906px"></div>
  <h3 class="heading abs" style="left:230px;top:915px;font-size:17px"><b>Comfortable Open Casual Spaces</b> <span>Or</span><br><span>Private Office Cubicles – At Your Option.</span></h3>
  <ul class="ticks" style="left:71px;top:977px;width:190px;font-size:7.5px;line-height:13px">
    <li style="margin-bottom:10px"><svg><use href="#tick"/></svg>Free Wifi.</li>
    <li style="margin-bottom:10px"><svg><use href="#tick"/></svg>24 hour access</li>
    <li style="margin-bottom:10px"><svg><use href="#tick"/></svg>Use of copier/printer (at per-copy cost).</li>
    <li style="margin-bottom:10px"><svg><use href="#tick"/></svg>Keyless, digital door entry.</li>
    <li style="margin-bottom:10px"><svg><use href="#tick"/></svg>Mail service.</li>
    <li style="margin-bottom:7px"><svg><use href="#tick"/></svg>Communal coffee bar and kitchen, with FREE coffee.</li>
    <li><svg><use href="#tick"/></svg>Free Wifi.</li>
  </ul>
  <ul class="ticks" style="left:281px;top:977px;width:200px;font-size:7.5px;line-height:13px">
    <li style="margin-bottom:10px"><svg><use href="#tick"/></svg>Free conference/presentation room, on a shared, scheduled basis. Outfitted with modern flat screen for presentations.</li>
    <li style="margin-bottom:10px"><svg><use href="#tick"/></svg>Private lockable lockers – at no extra cost.</li>
    <li style="margin-bottom:7px"><svg><use href="#tick"/></svg>Very comfortable private office chairs, that fully adjust and recline, with an extendable foot rest; comfortable couches and communal spaces.</li>
    <li><svg><use href="#tick"/></svg>Great opportunity for networking or mentoring.</li>
  </ul>
  <ul class="ticks" style="left:490px;top:977px;width:195px;font-size:7.5px;line-height:13px">
    <li style="margin-bottom:4px"><svg><use href="#tick"/></svg>Kitchen and bar area, with commercial sink, refrigerator, dishwasher, microwave, hand-washing station, spacious prep counters – for everyone’s use! Bring your lunch; refrigerate (but name tag) your drinks!</li>
    <li><svg><use href="#tick"/></svg>Weekly FREE happy hour with complimentary cocktails, beer and wine. A great opportunity to make new friends and business contacts.</li>
  </ul>

  <div class="num" style="left:71px;top:1230px">03</div>
  <div class="rule" style="left:71px;top:1280px"></div>
  <h3 class="heading abs" style="left:71px;top:1288px;font-size:17px"><b>Health And Social</b><br><span>Distance Amenities</span></h3>
  <ul class="dots" style="left:71px;top:1350px;width:190px">
    <li>Hand washing stations</li>
    <li>Distanced desks with glass or wall separations</li>
    <li>Rigorous cleaning and sanitizing schedules.</li>
    <li>Nightly ozone hospital-grade disinfection for all virus and bacteria.</li>
  </ul>
  <div class="photo" role="img" aria-label="Photo of the kitchen with steel refrigerator and grey cabinets" style="left:280px;top:1237px;width:193px;height:199px;background:linear-gradient(180deg,#5a5b5e 0%,#8c8d90 45%,#b8a98a 70%,#6e6a64 100%)"></div>
  <div class="photo" role="img" aria-label="Photo of long yellow desks under pendant lamps" style="left:490px;top:1237px;width:193px;height:199px;background:linear-gradient(180deg,#8e7448 0%,#b8b2a4 35%,#d9a52c 65%,#a47418 100%)"></div>

  <section class="cta">
    <h2 class="cta-title">Sign Up For Membership</h2>
    <div class="rule" style="left:337px;top:77px"></div>
    <p class="cta-text">Get your very own all-inclusive, fun,<br>personal business office environment.</p>
    <div class="btn">Get Membership</div>
  </section>

  <footer class="footer">
    <div class="f-map" role="img" aria-label="Faint map of the state"></div>
    <div class="f-brand"><b>DESKHAVEN</b><br>COSPACE</div>
    <p class="f-tag">Harborview’s first  shared business<br>co-working space</p>
    <p class="f-copy">©2020 Deskhaven. All Rights Reserved.<br>&nbsp;&nbsp;&nbsp;&nbsp;&nbsp;<span>Terms of Use | Privacy Policy</span></p>

    <div class="f-head" style="left:300px">Menu</div>
    <div class="rule" style="left:300px;top:60px"></div>
    <ul class="f-list" style="left:297px">
      <li class="on">Home</li><li>About</li><li>Amenities</li><li>Membership</li><li>Contact</li>
    </ul>

    <div class="f-head" style="left:444px">Social</div>
    <div class="rule" style="left:444px;top:60px"></div>
    <ul class="f-list" style="left:441px">
      <li>Friendwall</li><li>ProNetwork</li><li>Snapgram</li>
    </ul>

    <div class="f-head" style="left:588px">Contact</div>
    <div class="rule" style="left:588px;top:60px"></div>
    <ul class="f-list" style="left:585px">
      <li>418 Harbor St.</li><li>Ste. 101</li><li>Harborview, TX 77551</li><li>713-555-0142</li><li class="on">hello@deskhavenspace.com</li>
    </ul>
  </footer>
</main>
</body>
</html>
```